Home Page for a Swiss based start up company, trading Natural & Health food ingredients (B2B)

I would like to create a home page for my new start up company (Veltrana Swiss AG), the main field of activity is the trading and marketing of Natural and Health food ingredients towards the functional Food and Food supplements industry. (B2B).
Target Market : Functional Food and Food Supplement Manufacturers (B2B) based in Switzerland and Europe
The values I would like to convey are :
- sourcing of natural and health ingredients, (example : natural plant extracts, Omega 3, plant proteins, natural vitamins, vegan food ingredients...etc)
- Health & Nutritional Health
- Eco-friendly and Sustainability
- High Quality Standard in term of products and logistic services
- Trust and reliability
- Flexibility & speed to market
-Technical advice for the development of new products

The site will be translated in 3 languages (German, French, English)
Number of web pages : 5 : Home, About us, Products, Our Services, Contact

See here below attached Logo file.

Here some link of websites which can be taken as benchmark or source of inspiration
- https://quorbelix.com
- https://www.dralvimo.com/

Target Market(s)

Manufacturers of Functional Foods and Food Supplements in Switzerland and Europe (B2B)

Industry/Entity Type

B2B Trading of Natural & Health Ingredients

Coding

Number of Pages Required

Font styles to use
Sans Serif

Colors
0054AA
0677BA
7BADD7
CADEEF
E8F1F8
0094D4
00A9DD
6FCCEA
C7EBF8
E9F6FB
00AB8E
00BBA5
67D7C9
C6EFE9
E9F9F6
59FF00
82FF00
B8FF75
E3FFCB
F4FFEA
FFF300
FFF600
FEFA6F
FFFEC7
FFFEE8
FFC000
F8CF3A
FAE287
FDF2CF
FEFAEE
F0912C
F2A743
F7CA91
FBE8D2
FDF5EE
EE7325
F08F49
F5BC92
FAE3D3
FDF4ED

Requirements
Must have
• inspiration towards nature, sustainability, vegan food, functional food & beverages, food supplements, nutritional health, low carbon footprint
Should not have
• animals, chemistry, food additives

```html
<!DOCTYPE html>
<html lang="en">
<head>
<meta charset="utf-8">
<title>Veltrana Swiss – Natural &amp; Health Ingredients</title>
<link href="https://fonts.googleapis.com/css2?family=Nunito:wght@500;600;700&family=Lato:wght@400;700&display=swap" rel="stylesheet">
<style>
:root{
  --green:#169c7a;
  --green-dark:#0f8a6b;
  --green-soft:#2aa887;
  --ink:#111;
  --text:#555;
  --muted:#777;
  --field:#f1f1f1;
  --white:#fff;
  --black:#000;
}
*{box-sizing:border-box;margin:0;padding:0}
html,body{width:1200px;height:3908px;overflow:hidden}
body{position:relative;background:var(--white);font-family:"Lato",sans-serif;color:var(--text)}
.abs{position:absolute}
h1,h2,h3,.brand{font-family:"Nunito",sans-serif;color:var(--ink);font-weight:600}
.accent{color:var(--green)}
svg{display:block}

/* top bar & header */
.topbar{left:0;top:0;width:1200px;height:36px;background:var(--green);color:var(--white);font-size:15px;text-align:center;line-height:32px}
.header{left:0;top:36px;width:1200px;height:73px}
.header .brand{font-size:29px;left:110px;top:13px;white-space:nowrap}
.nav{left:346px;top:28px;display:flex;gap:30px;font-size:15px;color:#333;white-space:nowrap}
.nav .active{color:var(--green)}
.header-phone{left:892px;top:19px;display:flex;align-items:center;gap:10px;font-size:20px;color:var(--ink);font-family:"Nunito",sans-serif;font-weight:500;white-space:nowrap}
.round-icon{width:36px;height:36px;border-radius:50%;background:var(--green);display:flex;align-items:center;justify-content:center}

/* hero */
.hero{left:0;top:109px;width:1200px;height:603px;background:linear-gradient(100deg,#f3e6f0 0%,#e8ece6 35%,#d9dcd7 60%,#c8cfc9 100%)}
.hero-veg{left:0;top:480px;width:760px;height:123px;background:linear-gradient(90deg,#4f8a3a,#9b5a3a 45%,#c7403a 70%,rgba(200,80,60,0))}
.hero-ring{left:113px;top:162px;width:480px;height:480px;border-radius:50%;background:rgba(22,156,122,.55)}
.hero-circle{left:136px;top:185px;width:434px;height:434px;border-radius:50%;background:var(--green);text-align:center;color:var(--white)}
.hero-circle .pre{margin-top:88px;font-family:"Nunito",sans-serif;font-size:27px;font-weight:600}
.hero-circle .title{font-family:"Nunito",sans-serif;font-size:52px;font-weight:600;line-height:1.15;margin-top:2px;white-space:nowrap}
.hero-circle p{font-size:15px;line-height:26px;width:390px;margin:12px auto 0}
.btn-light{display:inline-block;margin-top:20px;background:var(--white);color:var(--green);font-weight:700;font-size:15px;border-radius:26px;padding:15px 32px}

/* welcome */
.welcome-title{left:0;top:770px;width:1200px;text-align:center;font-size:35px;font-weight:500}
.welcome-text{left:160px;top:830px;width:880px;text-align:center;font-size:15px;line-height:26px;color:var(--muted)}

/* values */
.values-title{left:110px;top:1010px;font-size:29px;font-weight:600;white-space:nowrap}
.values-list{left:110px;top:1072px;width:400px;list-style:none;font-size:15px;color:#333}
.values-list li{display:flex;gap:10px;line-height:25px;margin-bottom:11px}
.values-list svg{flex:none;margin-top:6px}
.btn{background:var(--green);color:var(--white);font-weight:700;font-size:15px;border-radius:26px;text-align:center}
.values-btn{left:112px;top:1365px;width:143px;height:52px;line-height:52px}
.values-block{left:625px;top:1086px;width:463px;height:331px;background:var(--green)}
.values-photo{left:546px;top:1006px;width:464px;height:328px;background:var(--white);box-shadow:0 6px 22px rgba(0,0,0,.18);padding:5px}
.values-photo div{width:100%;height:100%;background:radial-gradient(circle at 50% 30%,#9fb7a0 0%,#3f6f42 45%,#1f3d22 100%)}

/* services */
.services{left:0;top:1500px;width:1200px;height:636px;background:linear-gradient(120deg,#1b9a78,#148f6f 50%,#1a9677)}
.services-title{left:0;top:1562px;width:1200px;text-align:center;color:var(--white);font-size:35px}
.service-card{width:308px;height:416px;top:1647px;background:var(--white);border-radius:14px;overflow:hidden;text-align:center}
.service-card .photo{height:207px}
.service-card .badge{position:absolute;left:121px;top:173px;width:66px;height:66px;border-radius:50%;background:var(--green);border:4px solid var(--white);display:flex;align-items:center;justify-content:center}
.service-card h3{margin-top:46px;font-size:22px}
.service-card p{margin:12px auto 0;width:270px;font-size:15px;line-height:26px;color:var(--muted)}
.link{color:var(--green);font-size:15px;font-weight:400}
.service-card .link{display:block;margin-top:10px}

/* blog */
.blog-title{left:0;top:2205px;width:1200px;text-align:center;font-size:35px}
.blog-photo{left:141px;top:2294px;width:554px;height:529px;background:linear-gradient(180deg,#c9c3bc 0%,#d8cfc5 45%,#e8e2da 75%,#f0ece6 100%)}
.blog-feature{left:312px;top:2570px;width:362px;height:229px;background:var(--green);color:var(--white);padding:22px 24px}
.blog-feature h3{color:var(--white);font-size:24px}
.blog-feature .date{display:flex;align-items:center;gap:8px;font-size:16px;margin-top:10px}
.blog-feature p{font-size:14.5px;line-height:25px;margin-top:8px;hyphens:auto}
.blog-feature .more{margin-top:6px;font-size:15px}
.blog-card{left:728px;width:334px;height:254px;background:var(--white);box-shadow:0 2px 14px rgba(0,0,0,.1);border-bottom:3px solid var(--green);padding:22px 22px}
.blog-card h3{font-size:24px}
.blog-card .date{display:flex;align-items:center;gap:8px;font-size:16px;color:var(--muted);margin-top:14px}
.blog-card p{font-size:15px;line-height:26px;color:#444;margin-top:10px}
.blog-card .link{display:block;margin-top:6px}

/* contact */
.contact-title{left:0;top:2902px;width:1200px;text-align:center;font-size:35px}
.contact-text{left:200px;top:2960px;width:800px;text-align:center;font-size:15px;line-height:26px;color:var(--muted)}
.field{background:var(--field);border-radius:28px;font-size:15px;color:#999;padding-left:28px;line-height:51px;height:51px}
.field.area{border-radius:8px;height:143px;line-height:1;padding-top:24px}
.submit{left:132px;top:3348px;width:135px;height:46px;line-height:46px}
.touch-title{left:736px;top:3052px;font-size:28px}
.touch-item{left:740px;display:flex;gap:14px;font-size:15px;line-height:26px;color:#333;width:330px}
.touch-item svg{flex:none;margin-top:4px}
.social{width:42px;height:42px;border-radius:50%;border:1.5px solid var(--green)}
.social.on{background:var(--green)}

/* footer */
.footer{left:0;top:3466px;width:1200px;height:442px;background:var(--black);color:var(--white)}
.footer-brand{left:0;top:3510px;width:1200px;text-align:center;color:var(--white)!important;font-size:44px}
.footer-contact{left:0;top:3604px;width:1200px;display:flex;justify-content:center;gap:24px;font-size:15px;color:var(--white)}
.footer-contact span{display:flex;align-items:center;gap:10px}
.footer-social{width:54px;height:54px;border-radius:50%;background:#222;top:3673px}
.footer-social.on{background:var(--green)}
.footer-nav{left:0;top:3764px;width:1200px;display:flex;justify-content:center;gap:36px;font-size:16px;color:var(--white)}
.footer-rule{left:110px;top:3824px;width:980px;height:1px;background:#333}
.copyright{left:0;top:3855px;width:1200px;text-align:center;font-size:15px;color:var(--white)}
</style>
</head>
<body>

<div class="abs topbar">Lorem ipsum dolor sit amet, consectetur adipiscing elit</div>

<header class="abs header">
  <div class="abs brand">Veltrana Swiss</div>
  <nav class="abs nav">
    <span class="active">Home</span><span>About Us</span><span>Our Values</span><span>Our Services</span><span>Blog</span><span>Contact Us</span>
  </nav>
  <div class="abs header-phone">
    <span class="round-icon"><svg width="16" height="16" viewBox="0 0 24 24"><path fill="#fff" d="M6.6 10.8a15 15 0 0 0 6.6 6.6l2.2-2.2c.3-.3.7-.4 1-.2 1.1.4 2.3.6 3.6.6.6 0 1 .4 1 1V20c0 .6-.4 1-1 1A17 17 0 0 1 3 4c0-.6.4-1 1-1h3.5c.6 0 1 .4 1 1 0 1.3.2 2.5.6 3.6.1.3 0 .7-.2 1z"/></svg></span>
    +1 888 888 8888
  </div>
</header>

<section>
  <div class="abs hero" role="img" aria-label="Photo of a smiling woman chopping fresh vegetables in a bright kitchen"></div>
  <div class="abs hero-veg" role="img" aria-label="Fresh greens and tomatoes on the kitchen counter"></div>
  <div class="abs hero-ring"></div>
  <div class="abs hero-circle">
    <div class="pre">Welcome To</div>
    <div class="title">Veltrana Swiss</div>
    <p>Lorem ipsum dolor sit amet, consectetur adipiscing elit, sed do eiusmod tempor incididunt ut labore et dolore magna aliqua. Quis ipsum</p>
    <span class="btn-light">Get Started</span>
  </div>
</section>

<section>
  <h2 class="abs welcome-title">Welcome To <span class="accent">Veltrana Swiss</span></h2>
  <p class="abs welcome-text">Lorem ipsum dolor sit amet, consectetur adipiscing elit, sed do eiusmod tempor incididunt ut labore et dolore magna aliqua. Quis ipsum suspendisse ultrices gravida. Risus commodo viverra maecenas accumsan lacus vel facilisis. Lorem ipsum dolor sit amet, consectetur adipiscing elit, sed do eiusmod tempor incididunt ut labore et dolore magna aliqua. Quis ipsum suspendisse ultrices gravida. Risus commodo viverra maecenas accumsan lacus vel facilisis. Lorem ipsum dolor sit amet, consectetur adipiscing elit, sed do eiusmod tempor incididunt ut labore et dolore magna aliqua. Quis ipsum suspendisse ultrices</p>

  <h2 class="abs values-title">Veltrana Swiss <span class="accent">Values</span></h2>
  <ul class="abs values-list">
    <li><svg width="14" height="14" viewBox="0 0 14 14"><circle cx="7" cy="7" r="7" fill="#169c7a"/><path d="M4 7.2l2 2 4-4" stroke="#fff" stroke-width="1.8" fill="none"/></svg>Health &amp; Nutritional Health</li>
    <li><svg width="14" height="14" viewBox="0 0 14 14"><circle cx="7" cy="7" r="7" fill="#169c7a"/><path d="M4 7.2l2 2 4-4" stroke="#fff" stroke-width="1.8" fill="none"/></svg>Eco-friendly and Sustainability</li>
    <li><svg width="14" height="14" viewBox="0 0 14 14"><circle cx="7" cy="7" r="7" fill="#169c7a"/><path d="M4 7.2l2 2 4-4" stroke="#fff" stroke-width="1.8" fill="none"/></svg><span>High Quality Standard in term of products and<br>logistic services</span></li>
    <li><svg width="14" height="14" viewBox="0 0 14 14"><circle cx="7" cy="7" r="7" fill="#169c7a"/><path d="M4 7.2l2 2 4-4" stroke="#fff" stroke-width="1.8" fill="none"/></svg>Trust and reliability</li>
    <li><svg width="14" height="14" viewBox="0 0 14 14"><circle cx="7" cy="7" r="7" fill="#169c7a"/><path d="M4 7.2l2 2 4-4" stroke="#fff" stroke-width="1.8" fill="none"/></svg>Flexibility &amp; speed to market</li>
    <li><svg width="14" height="14" viewBox="0 0 14 14"><circle cx="7" cy="7" r="7" fill="#169c7a"/><path d="M4 7.2l2 2 4-4" stroke="#fff" stroke-width="1.8" fill="none"/></svg>Technical advice for the development of new products</li>
    <li><svg width="14" height="14" viewBox="0 0 14 14"><circle cx="7" cy="7" r="7" fill="#169c7a"/><path d="M4 7.2l2 2 4-4" stroke="#fff" stroke-width="1.8" fill="none"/></svg>Security of supply</li>
  </ul>
  <div class="abs btn values-btn">Learn More</div>
  <div class="abs values-block"></div>
  <div class="abs values-photo"><div role="img" aria-label="Forest canopy with green leaves and a faint CO2 symbol, evoking low carbon footprint"></div></div>
</section>

<section>
  <div class="abs services" role="img" aria-label="Green-tinted background photo of a person preparing food"></div>
  <h2 class="abs services-title">Our Services</h2>

  <article class="abs service-card" style="left:114px">
    <div class="photo" role="img" aria-label="Assorted fresh fruits and vegetables" style="background:linear-gradient(120deg,#5c8a3c,#b8452f 50%,#d98a3a)"></div>
    <span class="badge"><svg width="28" height="28" viewBox="0 0 24 24" fill="none" stroke="#fff" stroke-width="1.6"><rect x="5" y="4" width="14" height="17" rx="2"/><path d="M9 4h6v3H9zM8 11h8M8 15h5"/></svg></span>
    <h3>Lorem Ipsum</h3>
    <p>Lorem ipsum dolor sit amet, consectetur adipiscing elit, sed do eiusmod tempor incididunt.</p>
    <span class="link">Learn More &raquo;</span>
  </article>

  <article class="abs service-card" style="left:446px">
    <div class="photo" role="img" aria-label="Healthy bowl with avocado and greens" style="background:linear-gradient(120deg,#d9d9d6,#7a9a5a 45%,#1f6a6a 70%,#cfcfcc)"></div>
    <span class="badge"><svg width="28" height="28" viewBox="0 0 24 24" fill="none" stroke="#fff" stroke-width="1.6"><circle cx="12" cy="12" r="8"/><circle cx="12" cy="12" r="4"/></svg></span>
    <h3>Lorem Ipsum</h3>
    <p>Lorem ipsum dolor sit amet, consectetur adipiscing elit, sed do eiusmod tempor incididunt.</p>
    <span class="link">Learn More &raquo;</span>
  </article>

  <article class="abs service-card" style="left:777px">
    <div class="photo" role="img" aria-label="Table of grilled vegetable dishes" style="background:linear-gradient(120deg,#3a2a22,#8a5a32 45%,#c99a4a 70%,#4a3a2e)"></div>
    <span class="badge"><svg width="28" height="28" viewBox="0 0 24 24" fill="none" stroke="#fff" stroke-width="1.6"><path d="M4 13h16a8 8 0 0 1-16 0zM12 5v5M8 7v3M16 7v3"/></svg></span>
    <h3>Lorem Ipsum</h3>
    <p>Lorem ipsum dolor sit amet, consectetur adipiscing elit, sed do eiusmod tempor incididunt.</p>
    <span class="link">Learn More &raquo;</span>
  </article>
</section>

<section>
  <h2 class="abs blog-title">Our Blog</h2>
  <div class="abs blog-photo" role="img" aria-label="Woman in a kitchen holding a green apple beside fresh salad"></div>
  <article class="abs blog-feature">
    <h3>Lorem ipsum dolor sit</h3>
    <div class="date"><svg width="14" height="14" viewBox="0 0 14 14" fill="none" stroke="#fff" stroke-width="1.3"><rect x="1" y="2.5" width="12" height="10.5" rx="1"/><path d="M1 6h12M4 1v3M10 1v3"/></svg>April 27 2022</div>
    <p>Lorem ipsum dolor sit amet, consectetur adipiscing elit, sed do eiusmod tempor incid&shy;idunt ut labore et dolore Lorem ipsum dolor</p>
    <div class="more">Learn More</div>
  </article>

  <article class="abs blog-card" style="top:2294px">
    <h3>Lorem ipsum dolor sit</h3>
    <div class="date"><svg width="14" height="14" viewBox="0 0 14 14" fill="none" stroke="#169c7a" stroke-width="1.3"><rect x="1" y="2.5" width="12" height="10.5" rx="1"/><path d="M1 6h12M4 1v3M10 1v3"/></svg>April 27 2022</div>
    <p>Lorem ipsum dolor sit amet, consectetur adipiscing elit, sed do eiusmod tempor incididunt ut labore et dolore Lorem ipsum dolor sit amet</p>
    <span class="link">Learn More</span>
  </article>
  <article class="abs blog-card" style="top:2570px">
    <h3>Lorem ipsum dolor sit</h3>
    <div class="date"><svg width="14" height="14" viewBox="0 0 14 14" fill="none" stroke="#169c7a" stroke-width="1.3"><rect x="1" y="2.5" width="12" height="10.5" rx="1"/><path d="M1 6h12M4 1v3M10 1v3"/></svg>April 27 2022</div>
    <p>Lorem ipsum dolor sit amet, consectetur adipiscing elit, sed do eiusmod tempor incididunt ut labore et dolore Lorem ipsum dolor sit amet</p>
    <span class="link">Learn More</span>
  </article>
</section>

<section>
  <h2 class="abs contact-title">Contact Us</h2>
  <p class="abs contact-text">Lorem ipsum dolor sit amet, consectetur adipiscing elit, sed do eiusmod tempor incididunt ut labore et dolore magna aliqua. Quis ipsum suspendisse ultrices gravida.</p>

  <div class="abs field" style="left:132px;top:3054px;width:255px">First Name</div>
  <div class="abs field" style="left:403px;top:3054px;width:255px">Late Name</div>
  <div class="abs field" style="left:132px;top:3120px;width:255px">Email</div>
  <div class="abs field" style="left:403px;top:3120px;width:255px">Phone</div>
  <div class="abs field area" style="left:132px;top:3187px;width:526px">Messages</div>
  <div class="abs btn submit">Submit</div>

  <h3 class="abs touch-title">Get in Touch</h3>
  <div class="abs touch-item" style="top:3110px"><svg width="16" height="18" viewBox="0 0 24 24"><path fill="#169c7a" d="M12 2a7 7 0 0 0-7 7c0 5 7 13 7 13s7-8 7-13a7 7 0 0 0-7-7zm0 9.5A2.5 2.5 0 1 1 12 6.5a2.5 2.5 0 0 1 0 5z"/></svg><span>Lorem ipsum dolor sit amet, consectetur adipiscing elit</span></div>
  <div class="abs touch-item" style="top:3188px"><svg width="16" height="16" viewBox="0 0 24 24"><path fill="#169c7a" d="M6.6 10.8a15 15 0 0 0 6.6 6.6l2.2-2.2c.3-.3.7-.4 1-.2 1.1.4 2.3.6 3.6.6.6 0 1 .4 1 1V20c0 .6-.4 1-1 1A17 17 0 0 1 3 4c0-.6.4-1 1-1h3.5c.6 0 1 .4 1 1 0 1.3.2 2.5.6 3.6.1.3 0 .7-.2 1z"/></svg><span>+1 888 888 8888</span></div>
  <div class="abs touch-item" style="top:3236px"><svg width="17" height="14" viewBox="0 0 24 20"><path fill="#169c7a" d="M2 2h20v16H2zM2 3l10 8 10-8v2l-10 8L2 5z"/></svg><span>info@veltranaswiss.com</span></div>

  <div class="abs social on" style="left:737px;top:3291px"></div>
  <div class="abs social" style="left:785px;top:3291px"></div>
  <div class="abs social" style="left:833px;top:3291px"></div>
  <div class="abs social" style="left:883px;top:3291px"></div>
</section>

<footer>
  <div class="abs footer"></div>
  <div class="abs brand footer-brand">Veltrana Swiss</div>
  <div class="abs footer-contact">
    <span><svg width="10" height="14" viewBox="0 0 24 30"><path fill="#169c7a" d="M12 0a11 11 0 0 0-11 11c0 8 11 19 11 19s11-11 11-19A11 11 0 0 0 12 0zm0 15a4 4 0 1 1 0-8 4 4 0 0 1 0 8z"/></svg>123 Lorem ipsum dolor sit amet, consectetur</span>
    <span><svg width="13" height="13" viewBox="0 0 24 24"><path fill="#169c7a" d="M6.6 10.8a15 15 0 0 0 6.6 6.6l2.2-2.2c.3-.3.7-.4 1-.2 1.1.4 2.3.6 3.6.6.6 0 1 .4 1 1V20c0 .6-.4 1-1 1A17 17 0 0 1 3 4c0-.6.4-1 1-1h3.5c.6 0 1 .4 1 1 0 1.3.2 2.5.6 3.6.1.3 0 .7-.2 1z"/></svg>+1 888 888 8888</span>
    <span><svg width="15" height="12" viewBox="0 0 24 20"><path fill="#169c7a" d="M2 2h20v16H2zM2 3l10 8 10-8v2l-10 8L2 5z"/></svg>info@veltranaswiss.com</span>
  </div>
  <div class="abs footer-social" style="left:421px"></div>
  <div class="abs footer-social" style="left:496px"></div>
  <div class="abs footer-social on" style="left:572px"></div>
  <div class="abs footer-social" style="left:647px"></div>
  <div class="abs footer-social" style="left:722px"></div>
  <nav class="abs footer-nav"><span>Home</span><span>About Us</span><span>Our Values</span><span>Our Services</span><span>Blog</span><span>Contact Us</span></nav>
  <div class="abs footer-rule"></div>
  <div class="abs copyright">&copy; Copyrights 2022 Veltrana Swiss &nbsp;&nbsp;|&nbsp;&nbsp; All Rights Reserved</div>
</footer>

</body>
</html>
```